Medical consulting firm needs polished website

I am a physician and working on setting up a smal consulting firm in New Hampshire, USA. It is called Bright Harbor Medical Services, LLC and the website will be BrightHarborMed.com. I was puttering around at making my own website, and it just didn't come together nicely so I've decided to leave it to the pros. The focus of the business is Advanced Care Planning, ie planning for your future medical needs. So it deals with some heavy stuff like planning for if you get sick, who should make decisions for you, end of life options etc. So it can't be too flippant or cutesy, but also can't be too dour and dark. I am hoping to convey that by thinking ahead and making some plans you can lift some of the worries off of yourself and your family - and that we can help make a scary sounding path more manageable. I want it to be made with wordpress and I have actually already bought a template ( Vitarun – A Modern Multidisciplinary Medical & Health Theme ). The website needs to have general information about our services, doc profile, appointment maker, blog/url link page, and ideally web commerce application ( the template has access to woocommerce). I've posted my business card and current brochure (still tweaking them, but you get the idea). I am also partnering with lumenfold.com and so have included their logo and would want connections/info about them. I have the logos etc in different formats as needed.

Target Market(s)

middle aged to older adults

Industry/Entity Type

Medical

Coding

Coded - Design and coding required

Font styles to use
Sans Serif

Requirements
Must have
• as above.
Nice to have
• Ease of reading/access for elderly viewers. woo commerce.

```html
<!DOCTYPE html>
<html lang="en">
<head>
<meta charset="utf-8">
<title>Bright Harbor Medical Services</title>
<link href="https://fonts.googleapis.com/css2?family=Open+Sans:wght@300;400;600;700&family=Raleway:wght@300;400;600&display=swap" rel="stylesheet">
<style>
:root{
  --blue:#1c66b6;
  --blue-light:#2a78c4;
  --green:#2aa63f;
  --ink:#333;
  --muted:#777;
  --line:#e3e3e3;
  --pale:#f2f2f2;
  --white:#fff;
}
*{box-sizing:border-box;margin:0;padding:0}
html,body{width:1200px;height:3403px;overflow:hidden}
body{position:relative;background:var(--white);font-family:"Open Sans",Arial,sans-serif;color:var(--ink)}
.abs{position:absolute}
.brand{display:flex;align-items:center;gap:10px;color:var(--blue);font-weight:600;font-size:30px;font-family:"Open Sans",sans-serif}
.brand-dot{width:34px;height:34px;border-radius:50%;background:var(--blue)}
.info{font-size:11px;color:#555;line-height:17px}
.info small{color:#999;font-size:11px}
.social{display:flex;gap:5px;margin-top:4px}
.social span{width:15px;height:15px;border-radius:50%}
.nav{top:86px;left:0;width:1200px;height:39px;border-top:1px solid var(--line);border-bottom:1px solid var(--line)}
.nav a{position:absolute;top:0;height:38px;line-height:38px;font-size:11px;color:#333;text-decoration:none;text-transform:uppercase}
.nav .active{left:113px;width:73px;background:var(--green);color:#fff;text-align:center;font-weight:600}
.nav .book{left:771px;width:172px;background:var(--blue);color:#fff;text-align:center;font-weight:600}
.nav .search{left:953px;width:131px;border:1px solid var(--line);top:4px;height:30px;line-height:28px;padding-left:26px;color:#aaa;font-size:10px;text-transform:none}
.hero{top:125px;left:0;width:1200px;height:472px;background:linear-gradient(90deg,#eeeeee,#f6f6f6)}
.hero h1{position:absolute;left:113px;top:140px;font-family:"Raleway",sans-serif;font-weight:400;font-size:38px;line-height:51px;color:var(--blue-light)}
.btn-outline{position:absolute;border:1px solid var(--green);color:var(--green);font-size:12px;text-align:center}
.photo{position:absolute}
.dots{position:absolute;display:flex;gap:8px}
.dots span{width:11px;height:11px;border-radius:50%;border:1px solid #bbb}
.dots span.on{border-color:#888}
.section-title{position:absolute;font-family:"Raleway",sans-serif;font-weight:600;font-size:20px;color:var(--blue);letter-spacing:.5px}
.hours{left:685px;top:696px;width:399px;height:329px;background:var(--blue);color:#fff;padding:32px 36px}
.hours h3{font-family:"Raleway",sans-serif;font-weight:600;font-size:21px;margin-bottom:14px}
.hours p{font-size:11px;opacity:.85;line-height:17px;margin-bottom:34px;width:230px}
.hours .row{display:flex;justify-content:space-between;font-size:12px;padding:14px 0;border-bottom:1px solid rgba(255,255,255,.25)}
.hours .row:last-child{border:none}
.hours .row b{font-weight:600}
.quote-band{top:1089px;left:0;width:1200px;height:417px;background:linear-gradient(90deg,#5d5d5d,#6b6b6b 50%,#5a5a5a)}
.service{position:absolute;left:113px;display:flex;align-items:center;gap:30px}
.service .ic{width:74px;height:74px;border-radius:50%;border:1px solid #ddd;background:#fff;display:flex;align-items:center;justify-content:center}
.service p{font-size:13px;line-height:21px;color:#444;width:225px}
.features{top:2182px;left:0;width:1200px;height:535px;background:var(--pale)}
.card{position:absolute;top:2352px;width:292px;height:306px;background:#fff}
.card .img{height:208px}
.card h4{font-size:14px;font-weight:600;margin:22px 0 8px 24px;color:#333}
.card p{font-size:10px;color:#666;margin-left:24px}
.field{position:absolute;border:1px solid #ddd;font-size:11px;color:#999;padding-left:16px;line-height:43px;height:45px}
.btn-green{position:absolute;background:var(--green);color:#fff;font-weight:700;text-align:center;letter-spacing:1.5px}
.footer{top:3096px;left:0;width:1200px;height:307px;background:var(--blue);color:#fff}
.footer h5{position:absolute;font-size:10px;font-weight:700;text-transform:uppercase}
.footer .item{position:absolute;font-size:10px;display:flex;align-items:center;gap:10px;opacity:.9}
.foot-links{position:absolute;left:113px;top:265px;font-size:10px;display:flex;gap:14px;opacity:.85}
</style>
</head>
<body>

<!-- Header -->
<div class="abs brand" style="left:113px;top:22px"><span class="brand-dot"></span>Bright Harbor</div>
<div class="abs" style="left:515px;top:28px">
  <svg width="22" height="22" viewBox="0 0 22 22"><circle cx="11" cy="11" r="9" fill="none" stroke="#2a78c4" stroke-width="1.5"/><path d="M11 6v5l3 2" stroke="#2a78c4" stroke-width="1.5" fill="none"/></svg>
</div>
<div class="abs info" style="left:552px;top:28px">Monday - Friday 08:00 - 20:00<br><small>Saturday and Sunday - CLOSED</small></div>
<div class="abs" style="left:770px;top:28px">
  <svg width="16" height="24" viewBox="0 0 16 24"><rect x="2" y="1" width="12" height="22" rx="2" fill="none" stroke="#2a78c4" stroke-width="1.5"/><circle cx="8" cy="19" r="1.2" fill="#2a78c4"/></svg>
</div>
<div class="abs info" style="left:802px;top:28px">+ 0800 555 0143<br><small>office@brightharbormed.com</small></div>
<div class="abs" style="left:963px;top:30px">
  <svg width="26" height="22" viewBox="0 0 26 22"><circle cx="9" cy="12" r="7" fill="none" stroke="#2a78c4" stroke-width="1.5"/><circle cx="19" cy="7" r="5" fill="none" stroke="#2aa63f" stroke-width="1.5"/></svg>
</div>
<div class="abs info" style="left:1000px;top:26px">Follow us
  <div class="social"><span style="background:#3b5998"></span><span style="background:#1da1f2"></span><span style="background:#dd4b39"></span><span style="background:#0077b5"></span></div>
</div>

<nav class="abs nav">
  <a class="active">Home</a>
  <a style="left:220px">About us</a>
  <a style="left:324px">Services</a>
  <a style="left:435px">Blog</a>
  <a style="left:533px">Testimonials</a>
  <a style="left:662px">Contact us</a>
  <a class="book">
    <svg width="12" height="12" viewBox="0 0 12 12" style="vertical-align:-1px;margin-right:6px"><rect x="1" y="2" width="10" height="9" fill="none" stroke="#fff"/><path d="M1 5h10" stroke="#fff"/></svg>Book appointment</a>
  <a class="search">Search
    <svg width="10" height="10" viewBox="0 0 10 10" style="position:absolute;left:9px;top:10px"><circle cx="4" cy="4" r="3" fill="none" stroke="#aaa"/><path d="M6.5 6.5L9 9" stroke="#aaa"/></svg></a>
</nav>

<!-- Hero -->
<section class="abs hero">
  <h1>Advanced Care<br>Planning Specialists</h1>
  <div class="btn-outline" style="left:113px;top:272px;width:123px;height:43px;line-height:41px">Read More</div>
  <div class="photo" role="img" aria-label="Smiling family of four with children on the parents' shoulders" style="left:540px;top:15px;width:520px;height:457px;background:radial-gradient(ellipse at 55% 55%,#c9b8ad 0%,#d9d2cc 40%,#f2f2f2 72%)"></div>
  <div class="dots" style="left:555px;top:416px"><span></span><span class="on"></span><span></span><span></span></div>
</section>

<!-- Welcome -->
<h2 class="section-title" style="left:113px;top:643px">WELCOME TO OUR SITE</h2>
<div class="photo" role="img" aria-label="Family relaxing together on a sofa, video preview" style="left:113px;top:696px;width:538px;height:236px;background:linear-gradient(135deg,#cbbdb3,#a89a92 55%,#d8d0cb)">
  <svg width="76" height="76" viewBox="0 0 76 76" style="position:absolute;left:231px;top:80px"><circle cx="38" cy="38" r="35" fill="rgba(0,0,0,.2)" stroke="#fff" stroke-width="3"/><path d="M30 24l22 14-22 14z" fill="#fff"/></svg>
</div>
<p class="abs" style="left:113px;top:960px;font-size:13px;font-weight:700;color:#222">Advance care planning helps your voice to always be heard.</p>
<p class="abs" style="left:113px;top:990px;width:560px;font-size:10.5px;line-height:16px;color:#666">We are available to meet with you in the privacy of your own home or in our office and provide notary services. Sessions begin at 30 minutes and, if applicable, your insurance plan covers 80% of hourly costs.</p>
<div class="abs hours">
  <h3>WORKING HOURS</h3>
  <p>Is it us at our headquarters for a free consulting hour.</p>
  <div class="row"><b>Monday  -  Friday</b><span>9am - 5pm</span></div>
  <div class="row"><b>Saturday</b><span>9am - 1pm</span></div>
  <div class="row"><b>Sunday</b><span>Closed</span></div>
</div>

<!-- Testimonial -->
<section class="abs quote-band" role="img" aria-label="Muted photo of a family walking outdoors behind a client testimonial">
  <svg width="50" height="40" viewBox="0 0 50 40" style="position:absolute;left:575px;top:70px"><path d="M4 34c0-14 4-22 14-26l2 4c-6 3-8 7-8 12h8v10zM28 34c0-14 4-22 14-26l2 4c-6 3-8 7-8 12h8v10z" fill="#bdbdbd"/></svg>
  <p style="position:absolute;left:0;width:1200px;top:142px;text-align:center;color:#fff;font-size:17px;line-height:28px">Meet with you in the privacy of your own home or in our office and provide<br>notary services. Sessions begin at 30 minute.</p>
  <div style="position:absolute;left:501px;top:233px;width:198px;height:43px;border:1px solid #ccc;color:#fff;font-size:12px;line-height:41px;text-align:center">Daniel Marsh, England</div>
  <div class="dots" style="left:555px;top:341px"><span></span><span class="on" style="border-color:#eee"></span><span></span><span></span></div>
</section>

<!-- Services -->
<h2 class="section-title" style="left:116px;top:1552px">OUR SERVICES</h2>
<div class="abs" style="left:150px;top:1660px;width:1px;height:420px;background:#ddd"></div>
<div class="service" style="top:1619px"><span class="ic"><svg width="30" height="34" viewBox="0 0 30 34"><rect x="4" y="4" width="22" height="28" rx="2" fill="none" stroke="#2aa63f" stroke-width="2"/><rect x="10" y="1" width="10" height="6" fill="#fff" stroke="#2aa63f" stroke-width="2"/><path d="M8 20h4l2-5 3 9 2-4h4" fill="none" stroke="#2aa63f" stroke-width="1.8"/></svg></span><p>Individualized physician-guided<br>healthcare planning</p></div>
<div class="service" style="top:1721px"><span class="ic"><svg width="30" height="30" viewBox="0 0 30 30"><path d="M15 3v25M8 9h14M11 14c4 2 8 2 8 5s-8 3-8 6" fill="none" stroke="#2aa63f" stroke-width="2.2"/></svg></span><p>Helping navigate complex<br>medical situations</p></div>
<div class="service" style="top:1827px"><span class="ic"><svg width="30" height="32" viewBox="0 0 30 32"><path d="M5 3h14l6 6v20H5z" fill="none" stroke="#2aa63f" stroke-width="2"/><path d="M9 13h12M9 18h12M9 23h7" stroke="#2aa63f" stroke-width="1.8"/></svg></span><p>Creating legally binding<br>Advanced Directives</p></div>
<div class="service" style="top:1934px"><span class="ic"><svg width="30" height="30" viewBox="0 0 30 30"><circle cx="8" cy="15" r="4" fill="none" stroke="#2aa63f" stroke-width="2"/><circle cx="22" cy="7" r="4" fill="none" stroke="#2aa63f" stroke-width="2"/><circle cx="22" cy="23" r="4" fill="none" stroke="#2aa63f" stroke-width="2"/><path d="M11.5 13l7-4M11.5 17l7 4" stroke="#2aa63f" stroke-width="2"/></svg></span><p>Sharing your decisions with your<br>loved ones and your doctor</p></div>
<div class="service" style="top:2045px"><span class="ic"><svg width="26" height="30" viewBox="0 0 26 30"><path d="M7 13V9a6 6 0 0112 0v4" fill="none" stroke="#2aa63f" stroke-width="2.2"/><rect x="3" y="13" width="20" height="15" rx="2" fill="#2aa63f"/><circle cx="13" cy="20" r="2" fill="#fff"/></svg></span><p>Secure,accessible, web baces<br>storage of your documents</p></div>
<div class="photo" role="img" aria-label="Smiling family of four embracing" style="left:510px;top:1622px;width:556px;height:510px;background:radial-gradient(ellipse at 50% 50%,#c7b6ab 0%,#d8cfca 45%,#fff 72%)"></div>

<!-- Features -->
<section class="abs features">
  <p style="position:absolute;left:0;width:1200px;top:44px;text-align:center;font-size:11px;color:#555">Sub Heading</p>
  <h2 style="position:absolute;left:0;width:1200px;top:72px;text-align:center;font-family:'Raleway',sans-serif;font-weight:600;font-size:20px;color:var(--blue)">OUR FEATURES</h2>
  <div style="position:absolute;left:570px;top:112px;width:60px;height:2px;background:var(--blue)"></div>
</section>
<div class="card" style="left:113px"><div class="img" role="img" aria-label="Father carrying child on his shoulders in a sunny field" style="background:linear-gradient(180deg,#6fa4d8 0%,#a9c8e6 45%,#8eae4a 70%,#5f8a2c 100%)"></div><h4>Heading 1</h4><p>It is a long established fact that</p></div>
<div class="card" style="left:454px"><div class="img" role="img" aria-label="Parents laughing with their young son" style="background:linear-gradient(135deg,#d8cbc0,#a78b78 55%,#ece6e0)"></div><h4>Heading 2</h4><p>It is a long established fact that</p></div>
<div class="card" style="left:794px"><div class="img" role="img" aria-label="Family hugging together indoors" style="background:linear-gradient(135deg,#f0e6da,#c8aa95 50%,#e8ddd4)"></div><h4>Heading 3</h4><p>It is a long established fact that</p></div>

<!-- Newsletter -->
<h2 class="abs" style="left:0;width:1200px;top:2780px;text-align:center;font-family:'Raleway',sans-serif;font-weight:600;font-size:21px;color:var(--blue)">NEED HELP FINDING THE RIGHT DOCTOR?</h2>
<p class="abs" style="left:0;width:1200px;top:2820px;text-align:center;font-size:12px;color:#555">Get helpful information on what's important to you when choosing your kids pediatrician.</p>
<div class="field" style="left:265px;top:2876px;width:229px">Name</div>
<div class="field" style="left:510px;top:2876px;width:227px">E mail id</div>
<div class="btn-green" style="left:755px;top:2876px;width:163px;height:45px;line-height:45px;font-size:15px">SIGNUP!</div>
<div class="abs brand" style="left:494px;top:2984px;font-size:32px;font-weight:400;color:#2a4f7c"><span class="brand-dot" style="width:32px;height:32px;background:#2a4f7c"></span>lumenfold</div>

<!-- Footer -->
<footer class="abs footer">
  <div style="position:absolute;left:113px;top:52px;width:284px;height:100px;background:#fff;display:flex;align-items:center;justify-content:center">
    <div class="brand" style="font-size:27px"><span class="brand-dot"></span>Bright Harbor</div>
  </div>
  <h5 style="left:503px;top:52px">Contact Us</h5>
  <div class="item" style="left:503px;top:89px"><svg width="10" height="12" viewBox="0 0 10 12"><path d="M2 1h2l1 3-1.5 1a6 6 0 003 3L8 6.5l2 1v2.5C5 10 1 6 1 1z" fill="#fff"/></svg>603-555-0182</div>
  <div class="item" style="left:503px;top:112px"><svg width="10" height="12" viewBox="0 0 10 12"><path d="M5 11C2 7 1 5.5 1 4a4 4 0 018 0c0 1.5-1 3-4 7z" fill="#fff"/><circle cx="5" cy="4" r="1.4" fill="#1c66b6"/></svg>BrightHarborMed.com</div>
  <div class="item" style="left:503px;top:137px"><svg width="11" height="9" viewBox="0 0 11 9"><rect x=".5" y=".5" width="10" height="8" fill="none" stroke="#fff"/><path d="M.5.5l5 4 5-4" fill="none" stroke="#fff"/></svg>info@brightharbormed.com</div>
  <h5 style="left:753px;top:52px">Newsletter Signup!</h5>
  <div style="position:absolute;left:753px;top:84px;width:331px;height:43px;border:1px solid rgba(255,255,255,.7);font-size:10px;line-height:41px;padding-left:40px">E mail id
    <svg width="11" height="9" viewBox="0 0 11 9" style="position:absolute;left:16px;top:17px"><rect x=".5" y=".5" width="10" height="8" fill="none" stroke="#fff"/><path d="M.5.5l5 4 5-4" fill="none" stroke="#fff"/></svg></div>
  <div class="btn-green" style="left:982px;top:145px;width:102px;height:39px;line-height:39px;font-size:11px;letter-spacing:.5px">SIGNUP!</div>
  <div style="position:absolute;left:113px;top:238px;width:971px;height:1px;background:rgba(255,255,255,.25)"></div>
  <div class="foot-links"><span>Home</span>|<span>About us</span>|<span>Services</span>|<span>Blog</span>|<span>Testimonials</span>|<span>Contact us</span></div>
  <p style="position:absolute;right:116px;top:265px;font-size:10px;opacity:.85">Copyrights © 2016 All Rights Reserved</p>
</footer>

</body>
</html>
```